Meridian Crestline Motors *

Professional business cards for our auto wholesale dealership.

Target Market(s)

New and used cars sales managers and middle class to higher end private party buyers.

Industry/Entity Type

Automotive

Contact Information for Business Card

Meridian Crestline Motors
Darnell R Okonski
Owner
(555) 304-6618
mercrestmotors@quillbox.example
Dealer Lic # 48265

Logo Text

Meridian Crestline Motors, Mer Crest Motors, MCM, etc

Font styles to use
Serif
Sans Serif

Colors

Designer to choose colors to be used in the design.

Requirements
Must have
• A professional, but not pretentious, look
Nice to have
• It might be nice to see "MCM" in a shape form i.e. circle, triangle, etc in the corner or background somehwere
Should not have
• bright "girly" colors

```html
<!DOCTYPE html>
<html lang="en">
<head>
<meta charset="utf-8">
<title>Meridian Crestline Motors — Business Card</title>
<link rel="stylesheet" href="https://fonts.googleapis.com/css2?family=Open+Sans:wght@400;600;700&display=swap">
<style>
  :root{
    --bg:#2b2c2f;
    --card-dark:#262a31;
    --card-dark-2:#1c1f24;
    --lime:#a9d21c;
    --ink:#2b2f36;
    --paper:#f2f2f2;
    --paper-shade:#d9d9d9;
  }
  *{box-sizing:border-box;margin:0;padding:0}
  html,body{width:1200px;height:1200px;overflow:hidden;background:var(--bg)}
  body{position:relative;font-family:"Open Sans",Arial,sans-serif}

  .card{
    position:absolute;left:210px;width:780px;height:446px;border-radius:22px;overflow:hidden;
    background:linear-gradient(160deg,var(--card-dark) 0%,var(--card-dark-2) 100%);
    box-shadow:0 18px 40px rgba(0,0,0,.45);
  }
  .card--front{top:120px}
  .card--back{top:634px}

  /* front */
  .car-photo{position:absolute;border-radius:4px;
    background:radial-gradient(ellipse at 50% 55%,#c9cbcf 0%,#8d9197 40%,#3a3e45 75%,transparent 100%)}
  .car-photo--left{left:10px;top:8px;width:200px;height:170px}
  .car-photo--right{right:8px;top:8px;width:210px;height:175px}

  .front-name{
    position:absolute;left:0;right:0;top:62px;text-align:center;
    font-weight:700;font-size:46px;letter-spacing:3px;color:var(--lime);
  }

  .rule{position:absolute;left:0;right:0;height:8px;background:var(--lime)}
  .rule--top{top:190px}
  .rule--bottom{top:380px}

  .info-band{
    position:absolute;left:0;right:0;top:198px;height:182px;
    background:linear-gradient(180deg,var(--paper) 0%,var(--paper-shade) 100%);
    color:var(--ink);
  }
  .contact{position:absolute;display:flex;align-items:center;gap:10px;font-size:18px}
  .contact--phone{left:36px;top:24px}
  .contact--email{left:36px;top:128px}
  .contact__icon{width:24px;height:24px;flex:none}
  .person{position:absolute;left:0;right:0;top:58px;text-align:center}
  .person__name{font-weight:600;font-size:28px}
  .person__role{font-size:18px;margin-top:2px}
  .licence{position:absolute;right:36px;top:128px;font-size:18px}

  /* back */
  .back-photo{position:absolute;left:300px;top:0;width:480px;height:446px;
    background:radial-gradient(ellipse at 60% 45%,rgba(120,126,136,.35) 0%,rgba(60,64,72,.15) 50%,transparent 75%)}
  .back-brand{position:absolute;left:80px;top:140px;display:flex;align-items:center;gap:26px}
  .back-brand__dot{width:22px;height:22px;border-radius:50%;background:var(--lime);flex:none}
  .wordmark{color:var(--lime);font-weight:700;line-height:1.15}
  .wordmark__line{display:block;font-size:42px}
  .wordmark__line--sub{font-size:34px}
  .back-rule{position:absolute;left:0;right:0;top:370px;height:7px;background:var(--lime)}
</style>
</head>
<body>

<section class="card card--front" aria-label="Business card front">
  <div class="car-photo car-photo--left" role="img" aria-label="Photo of silver cars lined up"></div>
  <div class="car-photo car-photo--right" role="img" aria-label="Photo of silver cars lined up"></div>
  <div class="front-name">MCM</div>

  <div class="rule rule--top"></div>
  <div class="info-band">
    <div class="contact contact--phone">
      <svg class="contact__icon" viewBox="0 0 24 24"><circle cx="12" cy="12" r="12" fill="#2b2f36"/><path d="M8.5 6.5l2 2-1.2 1.5a7 7 0 0 0 4.7 4.7l1.5-1.2 2 2-1.3 1.8c-4.7-.3-9-4.6-9.3-9.3z" fill="#a9d21c"/></svg>
      <span>(555) 304-6618</span>
    </div>
    <div class="person">
      <div class="person__name">Darnell R Okonski</div>
      <div class="person__role">Owner</div>
    </div>
    <div class="contact contact--email">
      <svg class="contact__icon" viewBox="0 0 24 24"><circle cx="12" cy="12" r="12" fill="#2b2f36"/><rect x="6" y="8" width="12" height="8" fill="none" stroke="#a9d21c" stroke-width="1.6"/><path d="M6 8l6 5 6-5" fill="none" stroke="#a9d21c" stroke-width="1.6"/></svg>
      <span>mercrestmotors@quillbox.example</span>
    </div>
    <div class="licence">Dealer Lic # 48265</div>
  </div>
  <div class="rule rule--bottom"></div>
</section>

<section class="card card--back" aria-label="Business card back">
  <div class="back-photo" role="img" aria-label="Faint photo of a car in the background"></div>
  <div class="back-brand">
    <div class="back-brand__dot"></div>
    <div class="wordmark">
      <span class="wordmark__line">MERIDIAN CRESTLINE</span>
      <span class="wordmark__line wordmark__line--sub">Motors</span>
    </div>
  </div>
  <div class="back-rule"></div>
</section>

</body>
</html>
```